Personal training and nutrition business needs business card design

We need a business card that outlays our services and invites potential customers to join our team and take the first step to a healthier and more enjoyable life. We cater for any level of fitness and specialize in weight loss and conditioning, strength training, muscle gain and strength endurance. Whether you are just starting off or need some help getting to the next level of your journey we are here to get the job done.
We specialize in one on one or one on two personal training sessions and each program will be custom made to suit individual fitness goals of our clients

```html
<!DOCTYPE html>
<html lang="en">
<head>
<meta charset="utf-8">
<title>Pulse &amp; Pace – Business Card</title>
<link rel="stylesheet" href="https://fonts.googleapis.com/css2?family=Arimo:wght@400;700&family=Montserrat:wght@600&family=Oswald:wght@500&display=swap">
<style>
  :root {
    --stage: #222224;
    --card: #0c0b0d;
    --white: #f4f4f6;
    --grey: #c9c9cf;
    --violet: #8a4fc4;
    --orchid: #b35cc0;
    --divider: #2b2a2e;
  }
  * { box-sizing: border-box; margin: 0; padding: 0; }
  html, body { width: 1200px; height: 900px; overflow: hidden; }
  body {
    background: var(--stage);
    font-family: "Arimo", Arial, sans-serif;
    display: flex;
    flex-direction: column;
    align-items: center;
    justify-content: center;
    gap: 44px;
  }
  .card {
    width: 666px;
    height: 380px;
    background: var(--card);
    border-radius: 4px;
    box-shadow: 0 14px 34px rgba(0,0,0,.55);
    position: relative;
    display: flex;
  }
  /* front */
  .card-front .brand-panel {
    width: 47%;
    display: flex;
    flex-direction: column;
    align-items: center;
    justify-content: center;
  }
  .card-front .divider {
    width: 1px;
    background: var(--divider);
    margin: 26px 0;
  }
  .card-front .contact-panel {
    flex: 1;
    padding: 62px 30px 0 38px;
    color: var(--white);
  }
  .brand-mark {
    display: flex;
    flex-direction: column;
    align-items: center;
  }
  .brand-dot {
    width: 76px;
    height: 76px;
    border-radius: 50%;
    background: linear-gradient(135deg, var(--violet), var(--orchid));
    margin-bottom: 22px;
  }
  .brand-name {
    font-family: "Arimo", Arial, sans-serif;
    font-weight: 700;
    color: var(--white);
    font-size: 44px;
    line-height: 1;
    letter-spacing: 1px;
    text-transform: uppercase;
    text-align: center;
  }
  .brand-tagline {
    font-family: "Oswald", "Arial Narrow", sans-serif;
    font-weight: 500;
    font-size: 11px;
    letter-spacing: 1.6px;
    color: var(--orchid);
    margin-top: 10px;
    text-transform: uppercase;
  }
  .person-name {
    font-family: "Montserrat", Arial, sans-serif;
    font-weight: 600;
    font-size: 22px;
    letter-spacing: .5px;
    color: var(--violet);
    text-transform: uppercase;
  }
  .person-role { font-size: 16px; color: var(--white); margin-top: 4px; }
  .contact-list { list-style: none; margin-top: 20px; }
  .contact-list li {
    display: flex;
    align-items: center;
    gap: 9px;
    font-size: 17px;
    line-height: 1.55;
    color: var(--white);
  }
  .contact-list svg { width: 15px; height: 15px; flex: none; }
  .contact-list .accent { color: var(--orchid); }
  .address {
    margin-top: 18px;
    padding-left: 24px;
    font-size: 17px;
    line-height: 1.35;
    color: var(--grey);
  }
  /* back */
  .card-back { align-items: center; justify-content: center; }
  .card-back .brand-name { font-size: 50px; }
  .card-back .brand-tagline { font-size: 12px; }
</style>
</head>
<body>

<section class="card card-front">
  <div class="brand-panel">
    <div class="brand-mark">
      <div class="brand-dot"></div>
      <p class="brand-name">Pulse<br>&amp; Pace</p>
      <p class="brand-tagline">Personal Training. Nutrition. Motivation</p>
    </div>
  </div>
  <div class="divider"></div>
  <div class="contact-panel">
    <h1 class="person-name">Marcus Hale</h1>
    <p class="person-role">Managing Director</p>
    <ul class="contact-list">
      <li>
        <svg viewBox="0 0 16 16" aria-hidden="true"><path d="M4 1.5 6.2 4 5 5.6c.9 2 2.5 3.6 4.4 4.4L11 8.8l2.5 2.2-1.3 2.3C7 13 3 9 2.7 3.8Z" fill="none" stroke="#b35cc0" stroke-width="1.5" stroke-linejoin="round"/></svg>
        021-555 018 342
      </li>
      <li>
        <svg viewBox="0 0 16 16" aria-hidden="true"><rect x="1" y="3" width="14" height="10" rx="1" fill="#8a4fc4"/><path d="M1.5 3.5 8 9l6.5-5.5" fill="none" stroke="#0c0b0d" stroke-width="1.3"/></svg>
        hello@pulsepace.fit
      </li>
      <li>
        <svg viewBox="0 0 16 16" aria-hidden="true"><g fill="none" stroke="#8a4fc4" stroke-width="1.3"><circle cx="8" cy="8" r="6.5"/><ellipse cx="8" cy="8" rx="3" ry="6.5"/><path d="M1.5 8h13M2.5 4.8h11M2.5 11.2h11"/></g></svg>
        <span>www.<span class="accent">pulsepace</span>.fit</span>
      </li>
    </ul>
    <p class="address">17, Harbour Lane Riverside<br>30218, Eastland</p>
  </div>
</section>

<section class="card card-back">
  <div class="brand-mark">
    <div class="brand-dot"></div>
    <p class="brand-name">Pulse<br>&amp; Pace</p>
    <p class="brand-tagline">Personal Training. Nutrition. Motivation</p>
  </div>
</section>

</body>
</html>
```